Zenqo - revolutionary mobile payment

The app is a P2P money trasfert, without the using of credit card or bank circuits it can transfer electronic money from one person to another consumers simply and immediatelly.
You can use the color you want, but the message we need to transert to consumer is simplicity, safety and coolness.
In attach the logo of the company and the wireframe of thre page of the app.
The goal is to design the page of the app with a clear, simple and intuitive graphic.
Updates

I have upgrade the brief with important information and detail, many thanks

Target Market(s)

all the people

Industry/Entity Type

Credit Card

Requirements
Must have
• You have to design one icon for each button in the first page, (shop is: where to shop)
in the second one a new intuitive image (instead of the hand) that let the user to understand that with a simple swipe he can process the payment
Nice to have
• You can include or esxclude what you want or belive can improve user experience of the app
Should not have
• too much color, too much button or information

```html
<!DOCTYPE html>
<html lang="en">
<head>
<meta charset="utf-8">
<title>Zenqo – Home</title>
<link href="https://fonts.googleapis.com/css2?family=Questrial&display=swap" rel="stylesheet">
<style>
  :root{
    --page-bg:#c4c7cc;
    --status-bg:#0c0c0e;
    --nav-bg:#f4f4f5;
    --navy:#233768;
    --navy-deep:#1c2c58;
    --band-light:#6b7ea6;
    --tile:#2a3d6f;
    --tile-light:#3a5085;
    --white:#ffffff;
    --ink:#2b2b2f;
    --content-top:#e9e9eb;
    --content-mid:#b7b9bd;
  }
  *{box-sizing:border-box;margin:0;padding:0}
  html,body{width:1200px;height:1195px;overflow:hidden}
  body{background:var(--page-bg);font-family:'Questrial',sans-serif;position:relative}
  .screen{position:absolute;left:300px;top:65px;width:600px;height:1065px;overflow:hidden;
    background:linear-gradient(180deg,var(--content-top) 0%,var(--content-mid) 45%,#d8d9dc 70%,#efeff0 100%);
    box-shadow:0 20px 50px rgba(0,0,0,.25)}
  .status-bar{height:34px;background:var(--status-bg);color:var(--white);font-size:15px;
    display:flex;align-items:center;justify-content:space-between;padding:0 14px}
  .status-bar .carrier,.status-bar .battery{display:flex;align-items:center;gap:6px}
  .battery-cell{width:26px;height:12px;border:1.5px solid var(--white);border-radius:2px;position:relative}
  .battery-cell::after{content:"";position:absolute;left:1px;top:1px;width:5px;height:7px;background:var(--white)}
  .nav-bar{height:66px;background:var(--nav-bg);display:flex;align-items:center;justify-content:space-between;padding:0 20px}
  .brand{display:flex;align-items:center;gap:8px;color:var(--navy);font-size:30px}
  .brand-dot{width:22px;height:22px;border-radius:50%;background:var(--navy)}
  .profile-band{height:210px;position:relative;
    background:linear-gradient(160deg,var(--band-light) 0%,#4b5f8d 40%,var(--navy-deep) 100%)}
  .avatar{position:absolute;left:30px;top:40px;width:134px;height:134px;border-radius:50%;
    border:5px solid var(--white);background:radial-gradient(circle at 50% 40%,#8a7a66,#3e5a34 70%)}
  .profile-name{position:absolute;left:196px;top:74px;color:var(--white);font-size:34px}
  .profile-phone{position:absolute;left:198px;top:118px;color:#dfe4ef;font-size:17px;letter-spacing:1px}
  .edit-btn{position:absolute;right:28px;top:24px;width:40px;height:40px;border-radius:50%;background:var(--white);
    display:flex;align-items:center;justify-content:center}
  .tile{position:absolute;width:236px;height:214px;border-radius:6px;color:var(--white);font-size:24px;
    background:linear-gradient(150deg,var(--tile-light),var(--tile));box-shadow:0 10px 24px rgba(0,0,0,.35);
    display:flex;flex-direction:column;align-items:center;justify-content:center;gap:14px}
  .tile svg{width:110px;height:96px}
  .tile-ask{left:330px;top:285px}
  .tile-pay{left:50px;top:420px}
  .tile-shop{left:330px;top:555px}
  .tile-account{left:70px;top:690px}
</style>
</head>
<body>
<main class="screen">
  <div class="status-bar">
    <span class="carrier">●●●○○ NOVA</span>
    <span class="clock">4:21 PM</span>
    <span class="battery">22% <span class="battery-cell"></span></span>
  </div>
  <header class="nav-bar">
    <svg width="30" height="30" viewBox="0 0 24 24" aria-label="Settings"><path fill="#2b2b2f" d="M12 8a4 4 0 100 8 4 4 0 000-8zm9 5.5v-3l-2.4-.6a7 7 0 00-.8-1.9l1.3-2.1-2.1-2.1-2.1 1.3a7 7 0 00-1.9-.8L12.5 2h-3l-.6 2.4a7 7 0 00-1.9.8L4.9 3.9 2.8 6l1.3 2.1a7 7 0 00-.8 1.9L1 10.5v3l2.4.6c.2.7.4 1.3.8 1.9l-1.3 2.1 2.1 2.1 2.1-1.3c.6.4 1.2.6 1.9.8l.5 2.3h3l.6-2.4c.7-.2 1.3-.4 1.9-.8l2.1 1.3 2.1-2.1-1.3-2.1c.4-.6.6-1.2.8-1.9z"/><circle cx="12" cy="12" r="2.5" fill="#f4f4f5"/></svg>
    <div class="brand"><span class="brand-dot"></span>Zenqo</div>
  </header>
  <section class="profile-band">
    <div class="avatar" role="img" aria-label="User profile photo"></div>
    <h1 class="profile-name">Marlon Vesty</h1>
    <p class="profile-phone">+39 312 555 0198</p>
    <div class="edit-btn"><svg width="20" height="20" viewBox="0 0 20 20"><path d="M4 16l1-4 8-8 3 3-8 8z" fill="#2b2b2f"/></svg></div>
  </section>
  <a class="tile tile-ask">
    <svg viewBox="0 0 110 96"><rect x="10" y="30" width="90" height="56" rx="4" fill="#fff"/><path d="M10 34l45 30 45-30" stroke="#2a3d6f" stroke-width="4" fill="none"/><circle cx="82" cy="24" r="16" fill="#fff" stroke="#2a3d6f" stroke-width="3"/><text x="82" y="31" text-anchor="middle" font-size="20" fill="#2a3d6f" font-family="Questrial,sans-serif">€</text><path d="M30 6v22m-8-8l8 8 8-8" stroke="#fff" stroke-width="5" fill="none"/></svg>
    <span>Ask</span>
  </a>
  <a class="tile tile-pay">
    <svg viewBox="0 0 110 96"><rect x="6" y="22" width="98" height="60" rx="6" fill="#fff"/><rect x="6" y="34" width="98" height="10" fill="#2a3d6f"/><rect x="16" y="58" width="36" height="6" fill="#2a3d6f"/><path d="M62 66h32m-8-7l8 7-8 7" stroke="#2a3d6f" stroke-width="4" fill="none"/></svg>
    <span>Pay</span>
  </a>
  <a class="tile tile-shop">
    <svg viewBox="0 0 110 96"><path d="M8 26l30-10 34 10 30-10v64l-30 10-34-10-30 10z" fill="#fff"/><path d="M38 16v64M72 26v64" stroke="#2a3d6f" stroke-width="3"/><path d="M55 60c-10-14-14-20-14-28a14 14 0 0128 0c0 8-4 14-14 28z" fill="#2a3d6f" stroke="#fff" stroke-width="3"/><circle cx="55" cy="32" r="5" fill="#fff"/></svg>
    <span>Shop</span>
  </a>
  <a class="tile tile-account">
    <svg viewBox="0 0 110 96"><circle cx="55" cy="24" r="18" fill="#fff"/><path d="M18 92c0-26 14-40 37-40s37 14 37 40z" fill="#fff"/><path d="M55 54l-6 30h12z" fill="#2a3d6f"/><rect x="68" y="66" width="14" height="3" fill="#2a3d6f"/></svg>
    <span>Account</span>
  </a>
</main>
</body>
</html>
```